Residential home builder needs a fresh looking business card

We require a fresh looking business card for our business. We like the clean modern look. I have uploaded out logo and our email footer that incorporates some different elements. Blacks and Whites are good but i will leave this up to the design crowd creative minds.

our slogan is:
your idea of the perfect home

website (temporary site) but similar look and feel to the finished one
harbourlinehomes.com.au

We also have intentions to apply the same look and feel to the rest of our stationary (letterheads, envelopes, site signs, vehicles etc)

Industry/Entity Type

Home Builder

```html
<!DOCTYPE html>
<html lang="en">
<head>
<meta charset="utf-8">
<title>Harbourline Homes – Business Card</title>
<link rel="stylesheet" href="https://fonts.googleapis.com/css2?family=Arimo:wght@400;700&display=swap">
<style>
  :root {
    --stage: #e8e5de;
    --card-white: #ffffff;
    --card-yellow: #f6db1f;
    --brand-gold: #e9bd1c;
    --ink: #1d1d1b;
    --ink-soft: #4a4a48;
    --rule: #8a8a86;
  }
  * { box-sizing: border-box; margin: 0; padding: 0; }
  html, body {
    width: 1200px; height: 675px; overflow: hidden;
    background: var(--stage);
    font-family: "Arimo", Arial, sans-serif;
  }
  .stage {
    width: 1200px; height: 675px;
    display: flex; align-items: center; justify-content: center; gap: 40px;
  }
  .card {
    position: relative;
    width: 520px; height: 297px;
    box-shadow: 0 10px 24px rgba(0,0,0,0.18);
    overflow: hidden;
  }
  .card--front { background: var(--card-white); }
  .card--back {
    background: var(--card-yellow);
    display: flex; align-items: center; justify-content: center;
  }

  .wordmark {
    font-family: "Arimo", Arial, sans-serif;
    font-weight: 400;
    color: var(--ink);
    letter-spacing: 0.06em;
    text-transform: uppercase;
    line-height: 1;
    white-space: nowrap;
  }
  .card--front .wordmark {
    position: absolute; left: 34px; top: 104px;
    font-size: 20px;
  }
  .wordmark-rule {
    position: absolute; left: 34px; top: 133px;
    width: 230px; height: 1px; background: var(--rule);
  }
  .card--back .wordmark { font-size: 34px; }

  .feature-art {
    position: absolute; right: 0; top: 0;
    width: 210px; height: 205px;
    border-bottom-left-radius: 60px;
    background: linear-gradient(135deg, var(--brand-gold) 0%, #f3d873 40%, #3a3a38 70%, #1d1d1b 100%);
  }

  .contact {
    position: absolute; left: 48px; top: 152px;
    color: var(--ink-soft);
    font-size: 11.5px; line-height: 1.3;
  }
  .contact-name {
    color: var(--brand-gold);
    font-weight: 700; font-size: 15px;
  }
  .contact-role { margin-bottom: 12px; }
  .contact-address { margin-bottom: 6px; }
  .contact-line {
    display: flex; align-items: center; gap: 8px;
    margin-top: 3px;
  }
  .contact-line svg { width: 11px; height: 11px; flex: none; }
</style>
</head>
<body>
<main class="stage">
  <section class="card card--front" aria-label="Business card front">
    <div class="feature-art" role="img" aria-label="Large brand graphic area in gold and black tones"></div>
    <div class="wordmark">Harbourline Homes</div>
    <div class="wordmark-rule"></div>
    <div class="contact">
      <div class="contact-name">Jane Marlow</div>
      <div class="contact-role">President CEO</div>
      <div class="contact-address">418 Shoreline Dr,<br>Ste 12 Port Ellis,<br>NSW 2041 Australia</div>
      <div class="contact-line">
        <svg viewBox="0 0 12 12" aria-hidden="true"><path fill="var(--brand-gold)" d="M2.5 1h2l1 2.5-1.3 1a6 6 0 0 0 3.3 3.3l1-1.3 2.5 1v2a1 1 0 0 1-1 1A9.5 9.5 0 0 1 1.5 2a1 1 0 0 1 1-1z"/></svg>
        <span>+61 (02) 5550 1842</span>
      </div>
      <div class="contact-line">
        <svg viewBox="0 0 12 12" aria-hidden="true"><circle cx="6" cy="6" r="5" fill="none" stroke="var(--brand-gold)" stroke-width="1.4"/><path d="M1 6h10M6 1c-2.2 2.8-2.2 7.2 0 10M6 1c2.2 2.8 2.2 7.2 0 10" fill="none" stroke="var(--brand-gold)" stroke-width="1"/></svg>
        <span>www.harbourlinehomes.com.au</span>
      </div>
    </div>
  </section>

  <section class="card card--back" aria-label="Business card back">
    <div class="wordmark">Harbourline Homes</div>
  </section>
</main>
</body>
</html>
```